Calder Aviation website

We are an aviation company based in Miramar, FL but with worldwide coverage. We are involved in commercial aircraft (mostly freighters) trading, sale & leasing. Specifically, we specialized in freighters of the Veltram family (V316, V328, V335, V342, V359). We also assist with financing, sale/leaseback. Handle special aviation projects and provide consultancy services. Currently engaged in a Veltram 359 passenger to Freighter conversion (P2F).

Website Preliminary Initial Content/Sections as follows:

About Us
Founded in 2011, Calder Aviation's management has many years of experience in Aviation, a strong background in scheduled airlines with emphasis in all cargo operations, freight forwarding supply chain and freight logistics, as well as ACMI and CMI operations.

Calder’s focuses in facilitating wet and dry lease operations, charter and ACMI programs consultancy, aircraft sales, leasing and procurement, aviation consultancy and aircraft management.

Calder team is a hands-on reliable alternative that works toward achieving your aircraft and aviation objectives by meeting your requirements and timeframe throughout professional and personalized service.

Tiberio Salcedo has over three decades of experience in the aviation field including aircraft maintenance, airline management, supply chain and logistics management. Tiberio is a true entrepreneur with proven experience and expertise on the multiple facets of the commercial aviation industry throughout the creation and development of a cluster of aviation entities. Tiberio is the founder and former sole member/chairman of 64 Air, a Veltram 342 All-Cargo U.S. Certificated Air Carrier created from scratch in 2014 which nowadays conforms a superb growing airline platform with an immaculate compliance operational record.

Services

Aircraft Finance, Trading, Procurement and Leasing
Calder buys, sells, leases and facilitates aircraft trading while specializes in structured aircraft investment projects. Calder has deep industry relationships and years of expertise, allowing to successfully execute lease transactions. We assist airlines, financial institutions and leasing companies when selling or purchasing aircraft.

Aircraft Available for Sale/Lease

Sale/Leaseback
Sale-leaseback is a method of financing. If your company needs liquidity, your aircraft or engine can serve as collateral for a loan throughout a sale-leaseback transaction. Sale-leaseback can free the equity tied up in aircraft or asset. Even if there is no pressing need for funds, a sale-leaseback allows you to use the equity tied up in your aircraft in a more productive fashion. Leaseback arrangements are usually employed because they confer financing, accounting or taxation benefits.

Passenger to Freighter Conversion (P2F)
Pandemic has seen the resurgence of operators packing freight into the main cabins of passenger aircraft. Carriers have been allowed to transport cargo in the cabin by removing passenger seats completely. NAB/CARO have established exemptions that allow operators to fly in “Preighter” configuration for a limited time. Calder is closely working with a U.S. group that is developing a Class E Supplemental Type Certificate (STC) for applicability on V359 aircraft which will include a cargo door for containerized freight. Final approvals are expected during first quarter of 2022.
Wet lease
Throughout our deep relationships within the industry, Calder facilitates short or long-term wet leases to airlines and qualified parties around the globe, whereby we provide the Aircraft, Crews, Maintenance and Insurance (ACMI) worldwide services at competitive rates. We also specialize in AM leases where the aircraft is registered onto Lessee´s AOC with all maintenance services included in the rates, covering all maintenance risks, or CM or CMI where the client provides the aircraft.

Dry Lease
We offer aircraft from our own portfolio on dry lease or could engage in procuring the aircraft of your choice.

Asset & Aircraft Management
We provide aircraft owners Aircraft Management services, where we manage the technical side of the aircraft or the asset. Calder also provides Harlow Dynamics engines trading, repair and full management services. We also buy Veltram/Skylane surplus inventory.

Worldwide Charters
We facilitate the arrangement of full charters to airlines and logistics companies. Certain territory restrictions may apply.

Aviation Consultancy
We provide airline consultancy services for new or special projects. Calder also specializes on All Cargo International route analysis, implementation and development. Our team provides professional guidance in obtaining worldwide both scheduled and charter authority.

Target Market(s)

Our target market are the airlines, logistics companies and commercial aviation related entities

Industry/Entity Type

Commercial Aviation

Coding

Coded - Design and coding required

Number of Pages Required

3 page

Requirements
Must have
• Illustrations of wide body freighters such V359, V342, V328

```html
<!DOCTYPE html>
<html lang="en">
<head>
<meta charset="utf-8">
<title>Calder Aviation</title>
<link href="https://fonts.googleapis.com/css2?family=Marcellus&family=Roboto:wght@400;500;700&display=swap" rel="stylesheet">
<style>
:root{
  --navy:#070c33;
  --navy-2:#0d1545;
  --steel:#5f7489;
  --steel-light:#aab8c4;
  --mist:#e8e6e9;
  --text:#555a66;
  --white:#ffffff;
  --pill:#a9b6c2;
}
*{margin:0;padding:0;box-sizing:border-box}
html,body{width:1200px;height:3536px;overflow:hidden}
body{position:relative;background:var(--white);font-family:"Roboto",Arial,sans-serif;color:var(--text)}
.abs{position:absolute}
.serif{font-family:"Marcellus",Georgia,serif}

/* nav */
.topbar{left:0;top:0;width:1200px;height:80px;background:var(--navy);z-index:5}
.brand{left:144px;top:8px;width:215px;color:var(--white);font-family:"Marcellus",Georgia,serif;text-align:center;line-height:1}
.brand .word{font-size:32px;letter-spacing:1px;display:block}
.brand .sub{font-size:32px;letter-spacing:1px;display:block;margin-top:4px;transform:scale(.5);transform-origin:top center;letter-spacing:22px}
.nav{left:508px;top:30px;display:flex;gap:32px;font-size:14px;font-weight:500;color:var(--white)}
.nav .active{border-bottom:1px solid var(--steel-light);padding-bottom:10px}
.login{left:939px;top:19px;width:116px;height:42px;border-radius:21px;background:var(--pill);color:var(--navy);font-weight:700;font-size:15px;display:flex;align-items:center;justify-content:center}

/* hero */
.hero-photo{left:0;top:80px;width:1200px;height:650px}
.hero-title{left:144px;top:186px;color:var(--white);font-size:79px;line-height:96px;text-shadow:0 3px 8px rgba(0,0,0,.5)}
.btn{background:var(--navy);color:var(--white);font-weight:700;border-radius:40px;display:flex;align-items:center;justify-content:center}
.get-started{left:144px;top:404px;width:164px;height:55px;font-size:15px}
.slider-dots{left:1126px;top:284px;display:flex;flex-direction:column;gap:7px}
.slider-dots span{width:10px;height:10px;border-radius:50%;background:var(--white)}
.slider-dots span.off{background:transparent;border:1.5px solid var(--white)}

.marker{width:26px;height:26px;background:var(--steel);transform:rotate(45deg);border:3px solid var(--white)}

/* about */
.about-sky{left:0;top:760px;width:1200px;height:620px}
.about-photo{left:162px;top:804px;width:390px;height:390px;border-radius:50%;border:12px solid #9aa5b0}
.about-head{left:600px;top:818px;font-size:43px;color:var(--navy)}
.about-copy{left:600px;top:890px;width:430px;font-size:12.4px;line-height:24px;color:#5d6270}
.read-more{left:600px;top:1115px;width:164px;height:55px;font-size:15px}

/* services */
.services-head{left:0;top:1405px;width:1200px;text-align:center;font-size:43px;color:var(--navy)}
.card{top:1510px;width:293px;height:204px;border-radius:22px}
.card-label{top:1738px;width:293px;text-align:center;font-size:19px;font-weight:500;color:#2a2d38}
.services-copy{left:310px;top:1817px;width:580px;text-align:center;font-size:12.4px;line-height:24px;color:#5d6270}

/* available */
.avail-head{left:0;top:2166px;width:1200px;text-align:center;font-size:44px;line-height:54px;color:var(--navy)}
.offer{width:265px;font-size:11.6px;line-height:23px;color:#6a6e79}
.offer h3{font-size:18.5px;font-weight:500;color:#1d2030;line-height:22px;margin-bottom:14px}
.offer.left{left:111px;text-align:right}
.offer.right{left:835px;width:235px}
.small-btn{width:112px;height:38px;font-size:10.5px;border-radius:19px}

/* footer */
.footer-brand{left:144px;top:3390px;width:312px;color:var(--white);font-family:"Marcellus",Georgia,serif;text-align:center;line-height:1}
.footer-brand .word{font-size:46px;letter-spacing:2px;display:block}
.footer-brand .sub{font-size:46px;display:block;transform:scale(.45);transform-origin:top center;letter-spacing:30px;margin-top:6px}
.footer-nav{left:537px;top:3400px;display:flex;gap:22px;color:var(--white);font-size:17.5px;font-weight:500}
.footer-nav .sep{opacity:.9}
.legal{left:537px;top:3444px;color:var(--white);font-size:12.4px}
.social{left:537px;top:3486px;display:flex;gap:18px;color:var(--white);font-size:13px;font-weight:500}
</style>
</head>
<body>

<!-- navigation -->
<header class="abs topbar">
  <div class="abs brand"><span class="word">CALDER</span><span class="sub">AVIATION</span></div>
  <nav class="abs nav"><span class="active">HOME</span><span>ABOUT</span><span>SERVICES</span><span>AIRCRAFT AVAILABLE</span></nav>
  <div class="abs login">LOGIN</div>
</header>

<!-- hero -->
<svg class="abs" style="left:0;top:80px" width="1200" height="680" viewBox="0 80 1200 680">
  <defs>
    <linearGradient id="heroSky" x1="0" y1="0" x2="0" y2="1">
      <stop offset="0" stop-color="#7b8fb4"/>
      <stop offset=".45" stop-color="#6478a3"/>
      <stop offset=".75" stop-color="#8a96b0"/>
      <stop offset="1" stop-color="#c4cad6"/>
    </linearGradient>
  </defs>
  <polygon points="0,80 1200,80 1200,508 600,721 0,508" fill="#5f7489"/>
  <polygon points="0,80 1200,80 1200,495 600,706 0,495" fill="url(#heroSky)" role="img" aria-label="Wide-body freighter on a runway approach with a hillside city behind"/>
</svg>
<h1 class="abs hero-title serif">CALDER<br>AVIATION</h1>
<div class="abs btn get-started">GET STARTED</div>
<div class="abs slider-dots"><span></span><span class="off"></span><span></span><span></span></div>
<div class="abs marker" style="left:587px;top:711px"></div>

<!-- about -->
<svg class="abs about-sky" width="1200" height="620" viewBox="0 0 1200 620" role="img" aria-label="Freighter aircraft flying above soft clouds and mountain peaks">
  <defs>
    <linearGradient id="aboutSky" x1="0" y1="0" x2="0" y2="1">
      <stop offset="0" stop-color="#ffffff"/>
      <stop offset=".45" stop-color="#f3eeec"/>
      <stop offset=".7" stop-color="#d9dde5"/>
      <stop offset="1" stop-color="#bcc6d3"/>
    </linearGradient>
    <radialGradient id="warm" cx=".85" cy=".45" r=".35">
      <stop offset="0" stop-color="#f1d9c8"/>
      <stop offset="1" stop-color="#f1d9c8" stop-opacity="0"/>
    </radialGradient>
  </defs>
  <rect width="1200" height="620" fill="url(#aboutSky)"/>
  <rect width="1200" height="620" fill="url(#warm)"/>
</svg>
<div class="abs about-photo" role="img" aria-label="Cockpit instrument panel glowing at night" style="background:radial-gradient(circle at 50% 40%,#2b3566,#0d1230 70%)"></div>
<h2 class="abs about-head serif">ABOUT US</h2>
<p class="abs about-copy">Founded in 2011, Calder Aviation's management has many years of experience in Aviation, a strong background in scheduled airlines with emphasis in all cargo operations, freight forwarding supply chain and freight logistics, as well as ACMI and CMI operations.Calder’s focuses in facilitating wet and dry lease operations, charter and ACMI programs consultancy, aircraft sales, leasing and procurement, aviation consultancy and aircraft management.Calder team is a hands-on reliable alternative that works toward achieving your aircraft</p>
<div class="abs btn read-more">READ MORE</div>

<!-- services band -->
<svg class="abs" style="left:0;top:1255px" width="1200" height="810" viewBox="0 1255 1200 810">
  <polygon points="600,1268 1200,1462 1200,1868 600,2060 0,1868 0,1462" fill="#e8e6e9"/>
  <polyline points="0,1462 600,1268 1200,1462" fill="none" stroke="#c5d2dc" stroke-width="8"/>
</svg>
<div class="abs marker" style="left:587px;top:1250px"></div>
<h2 class="abs services-head serif">SERVICES</h2>
<div class="abs card" style="left:144px;background:linear-gradient(135deg,#c9b9a3,#7d6a58)" role="img" aria-label="Business people talking inside a private jet cabin"></div>
<div class="abs card" style="left:454px;background:linear-gradient(135deg,#0a2a63,#1b5fa6 55%,#06183f)" role="img" aria-label="Trading chart on a blue digital screen"></div>
<div class="abs card" style="left:763px;background:linear-gradient(135deg,#4d4f55,#25272d 60%,#c9cbd0)" role="img" aria-label="Hand signing a leasing contract"></div>
<div class="abs card-label" style="left:144px">Aircraft Finance</div>
<div class="abs card-label" style="left:454px">Trading</div>
<div class="abs card-label" style="left:763px">Procurement &amp; Leasing</div>
<p class="abs services-copy">Calder buys, sells, leases and facilitates aircraft trading while specializes in structured aircraft investment projects. Calder has deep industry relationships and years of expertise, allowing to successfully execute lease transactions. We assist airlines, financial institutions and leasing companies when selling or purchasing aircraft.</p>

<!-- aircraft available -->
<h2 class="abs avail-head serif">AIRCRAFT AVAILABLE<br>FOR SALE/LEASE</h2>

<svg class="abs" style="left:0;top:3000px" width="1200" height="536" viewBox="0 3000 1200 536">
  <defs>
    <linearGradient id="footSky" x1="0" y1="0" x2="0" y2="1">
      <stop offset="0" stop-color="#ffffff"/>
      <stop offset=".5" stop-color="#e4e2e6"/>
      <stop offset="1" stop-color="#b6bfcb"/>
    </linearGradient>
  </defs>
  <rect x="0" y="3000" width="1200" height="536" fill="url(#footSky)" role="img" aria-label="Wide-body freighter flying over a cloud layer"/>
  <polygon points="0,3380 600,3198 1200,3380 1200,3536 0,3536" fill="#5f7489"/>
  <polygon points="0,3405 600,3222 1200,3405 1200,3536 0,3536" fill="#070c33"/>
</svg>
<div class="abs marker" style="left:587px;top:3182px"></div>

<svg class="abs" style="left:390px;top:2360px" width="430" height="730" viewBox="390 2360 430 730">
  <defs>
    <linearGradient id="dLight" x1="0" y1="0" x2="0" y2="1">
      <stop offset="0" stop-color="#e3e6ea"/><stop offset="1" stop-color="#7d8b9a"/>
    </linearGradient>
    <linearGradient id="dDark" x1="0" y1="0" x2="0" y2="1">
      <stop offset="0" stop-color="#8b9aa9"/><stop offset="1" stop-color="#3c4d62"/>
    </linearGradient>
  </defs>
  <g>
    <polygon points="497,2369 593,2465 497,2561 401,2465" fill="url(#dLight)"/>
    <polygon points="714,2369 810,2465 714,2561 618,2465" fill="url(#dDark)"/>
    <polygon points="497,2629 593,2725 497,2821 401,2725" fill="url(#dDark)"/>
    <polygon points="714,2629 810,2725 714,2821 618,2725" fill="url(#dLight)"/>
    <polygon points="497,2889 593,2985 497,3081 401,2985" fill="url(#dLight)"/>
    <polygon points="714,2889 810,2985 714,3081 618,2985" fill="url(#dDark)"/>
  </g>
  <g fill="#ffffff">
    <!-- tag -->
    <path d="M470 2445 h26 l28 28 -22 22 -32 -32 z" />
    <circle cx="480" cy="2455" r="4" fill="#a9b4bf"/>
    <!-- plane -->
    <path d="M686 2465 l14 -3 10 -20 h7 l-5 20 h16 l6 -8 h5 l-3 11 3 11 h-5 l-6 -8 h-16 l5 20 h-7 l-10 -20 z"/>
    <!-- calendar -->
    <rect x="471" y="2700" width="52" height="50" rx="6"/>
    <rect x="480" y="2693" width="6" height="14" rx="2"/><rect x="508" y="2693" width="6" height="14" rx="2"/>
    <path d="M484 2731 l9 9 17 -17" fill="none" stroke="#56677b" stroke-width="6"/>
    <!-- users -->
    <circle cx="714" cy="2712" r="10"/><circle cx="692" cy="2718" r="7"/><circle cx="736" cy="2718" r="7"/>
    <path d="M696 2746 a18 18 0 0 1 36 0 z"/><path d="M678 2744 a14 12 0 0 1 22 -8 v8 z"/><path d="M750 2744 a14 12 0 0 0 -22 -8 v8 z"/>
    <!-- globe -->
    <g fill="none" stroke="#ffffff" stroke-width="5">
      <circle cx="497" cy="2985" r="26"/><ellipse cx="497" cy="2985" rx="11" ry="26"/>
      <line x1="471" y1="2985" x2="523" y2="2985"/><line x1="475" y1="2972" x2="519" y2="2972"/><line x1="475" y1="2998" x2="519" y2="2998"/>
    </g>
    <!-- monitor -->
    <rect x="684" y="2958" width="60" height="42" rx="4"/>
    <rect x="691" y="2965" width="46" height="28" fill="#506176"/>
    <rect x="708" y="3000" width="12" height="8"/><rect x="698" y="3008" width="32" height="5" rx="2"/>
  </g>
</svg>

<div class="abs offer left" style="top:2370px">
  <h3>Sale/Leaseback</h3>
  Sale-leaseback is a method of financing. If your company needs liquidity, your aircraft or engine can serve as collateral for a loan throughout a sale-leaseback transaction.
</div>
<div class="abs btn small-btn" style="left:265px;top:2519px">READ MORE</div>

<div class="abs offer right" style="top:2370px">
  <h3>Passenger to Freighter Conversion (P2F)</h3>
  Pandemic has seen the resurgence of operators packing freight into the main cabins of passenger aircraft.
</div>
<div class="abs btn small-btn" style="left:835px;top:2519px">READ MORE</div>

<div class="abs offer left" style="top:2630px">
  <h3>Dry Lease</h3>
  We offer aircraft from our own portfolio on dry lease or could engage in procuring the aircraft of your choice.
</div>
<div class="abs btn small-btn" style="left:265px;top:2779px">READ MORE</div>

<div class="abs offer right" style="top:2630px">
  <h3>Asset &amp; Aircraft Management</h3>
  We provide aircraft owners Aircraft Management services, where we manage the technical side of the aircraft
</div>
<div class="abs btn small-btn" style="left:835px;top:2779px">READ MORE</div>

<div class="abs offer left" style="top:2889px">
  <h3>Worldwide Charters</h3>
  We facilitate the arrangement of full charters to airlines and logistics companies. Certain territory restrictions may apply.
</div>
<div class="abs btn small-btn" style="left:265px;top:3039px">READ MORE</div>

<div class="abs offer right" style="top:2889px">
  <h3>Aviation Consultancy</h3>
  We provide airline consultancy services for new or special projects. Calder also specializes on All Cargo International route analysis, implementation
</div>
<div class="abs btn small-btn" style="left:835px;top:3039px">READ MORE</div>

<!-- footer -->
<footer>
  <div class="abs footer-brand"><span class="word">CALDER</span><span class="sub">AVIATION</span></div>
  <nav class="abs footer-nav"><span>HOME</span><span class="sep">/</span><span>ABOUT</span><span class="sep">/</span><span>SERVICES</span><span class="sep">/</span><span>AIRCRAFT AVAILABLE</span></nav>
  <div class="abs legal">© 2021 Calder Aviation. All rights reserved &nbsp;|&nbsp; Privacy &nbsp;|&nbsp; Terms of Use</div>
  <div class="abs social"><span>Flockpage</span><span>Chirpline</span><span>Workmesh</span></div>
</footer>

</body>
</html>
```